Construction Company Cellar Crafters needs Business Card

I would like modern looking business card design. I am attaching logo of our company. Please include cell nr 302.418.7650 , email address cellarcrafters4u@examplemail.com, web : cellarcrafters4u.com, please also include wording: Specializing in finishing and remodeling basements. You can play with dark grey and orange colors or any ideas are welcome. Also include social media icons Friendloop and HouseGuidr.

```html
<!DOCTYPE html>
<html lang="en">
<head>
<meta charset="utf-8">
<title>Cellar Crafters Business Card</title>
<link rel="stylesheet" href="https://fonts.googleapis.com/css2?family=Source+Sans+3:ital,wght@0,400;0,600;0,700;1,400&display=swap">
<style>
  :root {
    --bg-top: #acacac;
    --bg-bottom: #8e8e8e;
    --card-light: #ffffff;
    --card-dark: #131313;
    --accent: #f05a28;
    --ink: #2a2a2a;
    --on-dark: #ffffff;
  }
  * { margin: 0; padding: 0; box-sizing: border-box; }
  html, body { width: 1200px; height: 900px; overflow: hidden; }
  body {
    background: linear-gradient(to bottom, var(--bg-top), var(--bg-bottom));
    font-family: "Source Sans 3", "Myriad Pro", Arial, sans-serif;
    position: relative;
  }
  .card {
    position: absolute;
    top: 306px;
    width: 439px;
    height: 271px;
    border-radius: 12px;
  }
  .card--front { left: 149px; background: var(--card-light); }
  .card--back { left: 608px; background: var(--card-dark); }

  .brand-mark {
    position: absolute;
    left: 20px;
    top: 110px;
    width: 170px;
    color: var(--accent);
    font-weight: 700;
    font-size: 25px;
    line-height: 1.05;
    letter-spacing: 0.5px;
    text-transform: uppercase;
  }

  .contact { position: absolute; left: 211px; top: 56px; }
  .contact__name { color: var(--accent); font-weight: 600; font-size: 15.5px; line-height: 18px; }
  .contact__title { color: var(--ink); font-size: 12.5px; line-height: 15px; }
  .contact__list { list-style: none; margin-top: 22px; }
  .contact__item {
    display: flex; align-items: center; gap: 7px;
    color: var(--ink); font-size: 12.5px; line-height: 16px;
  }
  .contact__item svg { width: 9px; height: 9px; fill: var(--accent); flex: none; }

  .social { display: flex; gap: 12px; margin-top: 14px; padding-left: 2px; }
  .social__item {
    display: flex; align-items: center; gap: 4px;
    color: var(--accent); font-size: 12px; font-weight: 600;
  }
  .social__item::before {
    content: ""; width: 12px; height: 12px; background: var(--accent); border-radius: 1px;
  }

  .tagline {
    position: absolute; left: 0; right: 0; bottom: 34px;
    text-align: center; font-style: italic; font-size: 12px;
    color: var(--ink); text-transform: uppercase; letter-spacing: 0.1px;
  }

  .back-brand {
    position: absolute; left: 0; right: 0; top: 122px;
    text-align: center;
    color: var(--accent);
    font-weight: 700; font-size: 36px; letter-spacing: 2px;
    text-transform: uppercase;
  }
</style>
</head>
<body>
  <section class="card card--front" aria-label="Business card front">
    <div class="brand-mark">Cellar Crafters</div>

    <div class="contact">
      <p class="contact__name">Daniel Harper</p>
      <p class="contact__title">Managing Director</p>
      <ul class="contact__list">
        <li class="contact__item">
          <svg viewBox="0 0 10 10" aria-hidden="true"><path d="M2 0.5 L3.6 2.6 L2.8 3.6 Q4 6 6.4 7.2 L7.4 6.4 L9.5 8 L8.6 9.5 Q4.5 9.5 0.5 1.4 Z"/></svg>
          302.418.7650
        </li>
        <li class="contact__item">
          <svg viewBox="0 0 10 10" aria-hidden="true"><path d="M0.5 2 H9.5 V8.5 H0.5 Z M1.2 2.6 L5 5.4 L8.8 2.6" stroke="#fff" stroke-width="0.8"/></svg>
          cellarcrafters4u@examplemail.com
        </li>
        <li class="contact__item">
          <svg viewBox="0 0 10 10" aria-hidden="true"><circle cx="5" cy="5" r="4.5"/><path d="M5 0.5 V9.5 M0.5 5 H9.5" stroke="#fff" stroke-width="0.7"/></svg>
          cellarcrafters4u.com
        </li>
      </ul>
      <div class="social">
        <span class="social__item">Friendloop</span>
        <span class="social__item">HouseGuidr</span>
      </div>
    </div>

    <p class="tagline">Specializing in finishing and remodeling basements.</p>
  </section>

  <section class="card card--back" aria-label="Business card back">
    <p class="back-brand">Cellar Crafters</p>
  </section>
</body>
</html>
```